WordPress Website Design for Multi-Brand Aviation Group (Unified Branding System)

Project Overview:
We are seeking a professional, modern WordPress website design for an aviation-focused umbrella company that owns and operates multiple subsidiary businesses. The goal is to create a cohesive visual system that clearly communicates that each company operates under the same parent organization, while still allowing each brand to maintain a slightly distinct identity.
This is not just a single website design—we are looking for a scalable design framework that can be applied across multiple aviation-related businesses.
Objectives:
- Establish a consistent, recognizable brand identity across all company websites
Clearly communicate the relationship between the parent company and its subsidiaries
-bCreate a clean, high-end corporate aviation aesthetic
- Ensure all designs are SEO-friendly and optimized for performance
- Allow flexibility for future expansion (additional subsidiaries)
- Target Audience:
- Corporate aviation clients
- Charter customers
- Students wishing to receive flight training
- Aircraft owners and operators
- Turbine aircraft training to meet insurance requirements
- Business professionals and high-net-worth individuals
- Aviation industry partners
Design Direction & Style:
We are looking for a premium, professional aviation feel—think clean, modern, and high-trust. The design should reflect the standards of corporate aviation: precision, safety, and sophistication.
Key style notes:
Minimalist but impactful layout
High-quality aviation photography (jets, interiors, operations, global travel)
Subtle motion/interaction (hover effects, transitions)
Clear typography hierarchy for readability and professionalism
Branding Requirements:
Incorporate the primary colors of the parent company logo across all designs
Website Structure (Core Pages):
Design a system that includes:
Home Page with the following links:
- About / Company Overview
- Aircraft Management
- Aircraft Acquisition
- Charter
- Pilot Services
- Trip Support
- Contact Page
Site should further include:
- Mobile-first responsive design
- Fast-loading, performance-optimized layouts
SEO & Technical Considerations:
- Design should support high-level SEO implementation:
- Clean layout structure that translates well to semantic HTML
- Proper heading hierarchy (H1, H2, H3)
- Space for keyword-rich content without clutter
- Optimized image placement (with alt text capability)
- Fast load times (lightweight design approach)
- Compatibility with WordPress SEO plugins (e.g., Yoast or Rank Math)
WordPress Requirements:
- Design should be easily built using WordPress (preferred builders: Elementor, Gutenberg, or similar)
- Reusable templates for scalability across multiple sites
- Easy for non-developers to update text and images
- Modular components (blocks/sections that can be reused across pages and sites)
- Navigation & UX:
- Simple, intuitive navigation
- Sticky header preferred
Style guide including:
- Colors
- Fonts
- Button styles
- Layout system
- Designs similar to high-end corporate aviation, private jet charter, or luxury service brands are preferred—clean, sharp, and premium without being overly flashy.
What We Want to Avoid:
- Overly busy layouts
- Generic templates with no brand identity
- Outdated or “stock” looking aviation designs
- Poor mobile responsiveness
Additional Notes:
We are building a long-term brand system, not just a one-off website. There is potential for ongoing work as we expand additional subsidiary sites.
We value designers who understand branding consistency across multiple business units and can create a scalable, professional system.
Include the attached main company logo "Vireton Aviation Group" and the "Member PJFO" logo on the main page.

```html
<!DOCTYPE html>
<html lang="en">
<head>
<meta charset="utf-8">
<title>Vireton Aviation Group</title>
<link rel="stylesheet" href="https://fonts.googleapis.com/css2?family=Poppins:ital,wght@0,300;0,400;0,500;0,600;1,300&family=Prompt:wght@300;400&display=swap">
<style>
:root{
  --navy:#0b1f44;
  --navy-deep:#081836;
  --blue:#0b5cad;
  --blue-bright:#1167c4;
  --sky:#e6f1fb;
  --ink:#1c2433;
  --muted:#5b6577;
  --white:#ffffff;
  --gold:#f5b400;
  --line:#d9e2ee;
}
*{margin:0;padding:0;box-sizing:border-box}
html,body{width:1200px;height:3608px;overflow:hidden}
body{font-family:"Poppins",sans-serif;color:var(--ink);background:var(--white);position:relative}
.section{position:absolute;left:0;width:1200px}
.heading{font-family:"Prompt",sans-serif;font-weight:300;text-transform:uppercase;letter-spacing:1px}
.photo{position:absolute}
.btn{position:absolute;display:flex;align-items:center;justify-content:center;gap:10px;font-size:10.5px;font-weight:600;letter-spacing:.8px;text-transform:uppercase;height:37px;border-radius:2px}
.btn svg{width:16px;height:10px}
.btn-solid{background:var(--blue);color:var(--white)}
.btn-outline{border:1px solid rgba(255,255,255,.75);color:var(--white)}
.btn-white{background:var(--white);color:var(--blue)}

/* header */
.site-header{position:absolute;top:0;left:0;width:1200px;height:60px;border-bottom:1px solid rgba(255,255,255,.18);z-index:5;display:flex;align-items:center}
.brand{position:absolute;left:85px;display:flex;align-items:center;gap:8px;color:var(--white)}
.brand-mark{width:12px;height:12px;background:var(--blue-bright)}
.brand-name{font-size:14px;font-weight:500;letter-spacing:.5px}
.nav{position:absolute;left:275px;height:60px;border-left:1px solid rgba(255,255,255,.18);border-right:1px solid rgba(255,255,255,.18);width:650px;display:flex;align-items:center;gap:38px;padding-left:46px}
.nav a{color:var(--white);font-size:10.5px;letter-spacing:.6px;text-decoration:none;text-transform:uppercase}
.header-cta{left:964px;top:17px;width:117px;height:31px}
.search{position:absolute;left:1097px;top:24px}

/* hero */
.hero{top:0;height:606px;background:linear-gradient(180deg,#0d2a52 0%,#1f4f86 45%,#6f99c6 80%,#a9c3dd 100%)}
.hero .photo{inset:0}
.hero h1{position:absolute;left:83px;top:172px;color:var(--white);font-size:39px;line-height:47px}
.hero p{position:absolute;left:85px;top:328px;width:430px;color:#dbe6f4;font-size:11px;line-height:19px}
.hero .btn-solid{left:85px;top:389px;width:167px}
.hero .btn-outline{left:259px;top:389px;width:158px}

/* intro */
.intro{top:606px;height:780px;background:linear-gradient(180deg,#fff 0%,#fff 55%,#eaf3fc 80%,#d8e9f8 100%)}
.frame-lines{position:absolute;left:85px;top:0;width:1027px;height:100%;border-left:1px solid var(--line);border-right:1px solid var(--line)}
.feature-card{position:absolute;top:63px;width:506px;height:325px;color:var(--white);text-align:center}
.feature-card .photo{inset:0}
.feature-card h3{position:absolute;left:0;right:0;bottom:56px;font-size:17px;font-weight:600;letter-spacing:.5px}
.feature-card p{position:absolute;left:0;right:0;bottom:35px;font-size:11px;font-weight:300}
.why-title{position:absolute;left:0;width:1200px;top:445px;text-align:center;font-size:26px;color:var(--ink)}
.timeline{position:absolute;left:151px;top:502px;width:908px;border-top:1px dotted #9aa7b8}
.why-item{position:absolute;top:503px;width:180px;text-align:center}
.why-item .stem{width:1px;height:40px;background:#9aa7b8;margin:0 auto}
.why-item .dot{width:7px;height:7px;border-radius:50%;background:var(--blue);margin:-2px auto 0}
.why-item .num{font-size:10.5px;font-weight:600;margin-top:8px}
.why-item .circle{width:106px;height:106px;border-radius:50%;background:rgba(207,226,245,.75);margin:6px auto 0;display:flex;align-items:center;justify-content:center}
.why-item .circle svg{width:48px;height:48px}
.why-item h4{font-size:13px;font-weight:500;line-height:17px;margin-top:18px}

/* services */
.services{top:1386px;height:546px;background:radial-gradient(ellipse at 50% 0%,#17386a 0%,var(--navy) 55%,var(--navy-deep) 100%)}
.services h2{position:absolute;top:60px;left:0;width:1200px;text-align:center;color:var(--white);font-size:26px}
.service-card{position:absolute;top:116px;height:360px;color:var(--white)}
.service-card .photo{inset:0}
.service-card h3{position:absolute;left:22px;bottom:56px;font-size:14px;font-weight:500}
.service-card p{position:absolute;left:22px;bottom:22px;width:200px;font-size:10.5px;line-height:14px;font-weight:300}
.service-card .go{position:absolute;right:22px;bottom:20px;width:28px;height:28px;border:1px solid var(--white);border-radius:50%;display:flex;align-items:center;justify-content:center}

/* unified */
.unified{top:1932px;height:539px;background:linear-gradient(180deg,#ffffff 0%,#e5eef8 25%,#a6bfd8 50%,#4b6f98 70%,#2b4c72 100%);text-align:center}
.unified .photo{inset:0}
.unified h2{position:absolute;top:150px;left:0;width:1200px;font-size:26px;color:var(--ink)}
.unified p{position:absolute;top:195px;left:220px;width:760px;font-size:11px;line-height:19px;color:#2f3848}
.unified .btn-white{left:427px;top:262px;width:180px;box-shadow:0 2px 6px rgba(0,0,0,.08)}
.unified .btn-outline{left:615px;top:262px;width:158px;border-color:#5d6e85;color:#23324a}

/* testimonial */
.testimonial{top:2471px;height:525px;background:linear-gradient(180deg,#fff 0%,#fff 70%,#e4f0fb 100%)}
.testimonial .pilot{left:85px;top:63px;width:597px;height:396px}
.quote-box{position:absolute;left:682px;top:63px;width:430px;height:396px;background:var(--white);border:1px solid #eef1f5;border-left:none}
.quote-box h2{position:absolute;left:52px;top:40px;font-size:28px;line-height:35px;color:var(--ink);width:340px}
.quote-box h2 span{color:var(--blue)}
.reviewer{position:absolute;left:52px;top:176px;display:flex;gap:17px;align-items:center}
.avatar{width:36px;height:36px;border-radius:50%;background:#7f93ad;border:2px solid var(--blue)}
.reviewer strong{display:block;font-size:14px;font-weight:600}
.reviewer small{font-size:9px;color:var(--muted)}
.quote-box blockquote{position:absolute;left:52px;top:234px;width:340px;font-size:13px;line-height:21px;font-style:italic;font-weight:300;color:#4a5366}
.stars{position:absolute;left:52px;top:325px;display:flex;gap:5px}
.quote-mark{position:absolute;right:18px;bottom:12px}

/* cta */
.cta{top:2996px;height:326px;background:linear-gradient(180deg,#0b5cad 0%,#0a58a8 60%,#0a4f99 100%);text-align:center;overflow:hidden}
.cta h2{position:absolute;top:72px;left:0;width:1200px;color:var(--white);font-size:26px}
.cta p{position:absolute;top:112px;left:0;width:1200px;color:#dbe7f6;font-size:11px}
.cta .btn-white{left:406px;top:143px;width:192px}
.cta .btn-outline{left:605px;top:143px;width:190px}
.cta-word{position:absolute;left:0;width:1200px;top:222px;font-family:"Poppins",sans-serif;font-weight:600;font-size:104px;letter-spacing:10px;color:rgba(255,255,255,.08);line-height:1}

/* footer */
.site-footer{top:3322px;height:286px;background:var(--navy-deep);color:#c9d3e2}
.footer-brand{position:absolute;left:85px;top:44px;display:flex;align-items:center;gap:8px;color:var(--white)}
.footer-about{position:absolute;left:85px;top:103px;width:180px;font-size:9.5px;line-height:16px}
.socials{position:absolute;left:85px;top:181px;display:flex;gap:10px}
.socials span{width:22px;height:22px;border:1px solid #c9d3e2;border-radius:50%}
.fcol{position:absolute;top:46px;font-size:9.5px}
.fcol h5{color:var(--white);font-size:10.5px;font-weight:500;letter-spacing:.6px;margin-bottom:10px}
.fcol li{list-style:none;line-height:20.5px}
.fdiv{position:absolute;top:32px;width:1px;height:176px;background:rgba(255,255,255,.12)}
.contact-row{display:flex;gap:10px;align-items:flex-start;margin-bottom:16px;width:170px;line-height:15px}
.contact-row i{flex:0 0 20px;height:20px;border:1px solid #c9d3e2;border-radius:50%;display:flex;align-items:center;justify-content:center}
.contact-row a{color:#4a9be8;text-decoration:none}
.email-field{width:158px;height:33px;border:1px solid rgba(255,255,255,.25);font-size:9.5px;padding:10px 14px;color:#c9d3e2;margin-top:4px}
.sub-btn{position:relative;margin-top:12px;width:118px;height:34px;font-size:9.5px;background:var(--blue)}
.member{display:flex;align-items:center;gap:8px;margin-top:12px}
.member .badge{width:26px;height:26px;border-radius:50%;background:#2a74c6}
.member b{color:var(--white);font-size:13px;font-weight:500;letter-spacing:1px}
.member small{display:block;font-size:7px;color:#c9d3e2}
.footer-rule{position:absolute;left:85px;top:230px;width:1027px;height:1px;background:rgba(255,255,255,.15)}
.copyright{position:absolute;top:249px;left:0;width:1200px;text-align:center;font-size:9.5px}
</style>
</head>
<body>

<header class="site-header">
  <div class="brand"><span class="brand-mark"></span><span class="brand-name">Vireton Aviation Group</span></div>
  <nav class="nav">
    <a href="#">About &#8964;</a><a href="#">Aircraft Management</a><a href="#">Aircraft Acquisition</a><a href="#">Charter</a><a href="#">Pilot Services</a>
  </nav>
  <a class="btn btn-solid header-cta" href="#">Contact Us <svg viewBox="0 0 16 10"><path d="M1 5h13M10 1l4 4-4 4" stroke="#fff" fill="none" stroke-width="1.4"/></svg></a>
  <svg class="search" width="14" height="14" viewBox="0 0 14 14"><circle cx="6" cy="6" r="4.5" stroke="#fff" fill="none" stroke-width="1.3"/><path d="M9.5 9.5L13 13" stroke="#fff" stroke-width="1.3"/></svg>
</header>

<section class="section hero">
  <div class="photo" role="img" aria-label="Private business jet flying above a sea of clouds at altitude" style="background:radial-gradient(ellipse at 72% 40%,rgba(230,238,248,.35) 0%,rgba(0,0,0,0) 45%),linear-gradient(90deg,rgba(8,24,54,.55) 0%,rgba(8,24,54,0) 55%)"></div>
  <h1 class="heading">Elevating Aviation<br>Excellence Across<br>Every Operation</h1>
  <p>A unified aviation group delivering world-class aircraft management, charter, acquisition, and pilot services—built on precision, safety, &amp; trust.</p>
  <a class="btn btn-solid" href="#">Request a Charter <svg viewBox="0 0 16 10"><path d="M1 5h13M10 1l4 4-4 4" stroke="#fff" fill="none" stroke-width="1.4"/></svg></a>
  <a class="btn btn-outline" href="#">Explore Services <svg viewBox="0 0 16 10"><path d="M1 5h13M10 1l4 4-4 4" stroke="#fff" fill="none" stroke-width="1.4"/></svg></a>
</section>

<section class="section intro">
  <div class="frame-lines"></div>
  <article class="feature-card" style="left:85px">
    <div class="photo" role="img" aria-label="Pilot and crew member reviewing paperwork beside a private jet" style="background:linear-gradient(180deg,#9aa4ad 0%,#6c757e 50%,#1d2430 100%)"></div>
    <h3>Aircraft Management</h3>
    <p>Seamless ownership experience with full-service operational oversight.</p>
  </article>
  <article class="feature-card" style="left:606px">
    <div class="photo" role="img" aria-label="Business traveller on the phone inside a private jet cabin" style="background:linear-gradient(180deg,#b9b2aa 0%,#857c74 50%,#1f1d1e 100%)"></div>
    <h3>Aircraft Acquisition</h3>
    <p>Strategic sourcing and advisory for buying and selling aircraft.</p>
  </article>

  <h2 class="heading why-title">Why Choose Us</h2>
  <div class="timeline"></div>
  <div class="why-item" style="left:86px">
    <div class="stem"></div><div class="dot"></div><div class="num">01</div>
    <div class="circle"><svg viewBox="0 0 48 48" fill="none" stroke="#0b5cad" stroke-width="1.8"><rect x="6" y="14" width="36" height="26" rx="3"/><path d="M18 14v-4h12v4"/><circle cx="24" cy="27" r="7"/><path d="M24 23v8M20 27h8"/></svg></div>
    <h4>Safety-First<br>Operational Standards</h4>
  </div>
  <div class="why-item" style="left:300px">
    <div class="stem"></div><div class="dot"></div><div class="num">02</div>
    <div class="circle"><svg viewBox="0 0 48 48" fill="none" stroke="#0b5cad" stroke-width="1.8"><path d="M24 4l5 4 6-1 2 6 5 3-2 6 2 6-5 3-2 6-6-1-5 4-5-4-6 1-2-6-5-3 2-6-2-6 5-3 2-6 6 1z"/><circle cx="24" cy="24" r="9"/><path d="M20 24l3 3 5-6"/></svg></div>
    <h4>Experienced Aviation<br>Professionals</h4>
  </div>
  <div class="why-item" style="left:513px">
    <div class="stem"></div><div class="dot"></div><div class="num">03</div>
    <div class="circle"><svg viewBox="0 0 48 48" fill="none" stroke="#0b5cad" stroke-width="1.8"><path d="M10 30l10-12 6 4 6-6 8 10-10 10-6-4-6 4z"/><path d="M18 8l2 4M24 6v5M30 8l-2 4"/></svg></div>
    <h4>Global Reach<br>&amp; 24/7 Support</h4>
  </div>
  <div class="why-item" style="left:727px">
    <div class="stem"></div><div class="dot"></div><div class="num">04</div>
    <div class="circle"><svg viewBox="0 0 48 48" fill="none" stroke="#0b5cad" stroke-width="1.8"><circle cx="24" cy="16" r="5"/><circle cx="12" cy="22" r="4"/><circle cx="36" cy="22" r="4"/><path d="M15 38c0-6 4-10 9-10s9 4 9 10M5 38c0-5 3-8 7-8M43 38c0-5-3-8-7-8"/></svg></div>
    <h4>Tailored<br>Client Solutions</h4>
  </div>
  <div class="why-item" style="left:942px">
    <div class="stem"></div><div class="dot"></div><div class="num">05</div>
    <div class="circle"><svg viewBox="0 0 48 48" fill="none" stroke="#0b5cad" stroke-width="1.8"><circle cx="24" cy="24" r="6"/><path d="M24 12v-3M24 39v-3M12 24H9M39 24h-3M15.5 15.5l-2-2M34.5 34.5l-2-2M15.5 32.5l-2 2M34.5 13.5l-2 2"/><path d="M8 30a17 17 0 0 0 30 4M40 18a17 17 0 0 0-30-4"/></svg></div>
    <h4>Transparent,<br>Efficient Processes</h4>
  </div>
</section>

<section class="section services">
  <h2 class="heading">Our Services</h2>
  <article class="service-card" style="left:0;width:392px">
    <div class="photo" role="img" aria-label="Ground crew loading baggage onto an airliner on the apron" style="background:linear-gradient(180deg,#b8c6d3 0%,#7d8791 55%,#1a2230 100%)"></div>
    <h3>Charter Services</h3>
    <p>Flexible, global private travel solutions tailored to your schedule.</p>
    <span class="go"><svg width="12" height="12" viewBox="0 0 12 12"><path d="M1 6h9M7 3l3 3-3 3" stroke="#fff" fill="none" stroke-width="1.2"/></svg></span>
  </article>
  <article class="service-card" style="left:406px;width:391px">
    <div class="photo" role="img" aria-label="Pilot with headset seated at the controls in a cockpit" style="background:linear-gradient(180deg,#a7a9a8 0%,#5b5e60 50%,#14181f 100%)"></div>
    <h3>Pilot Services</h3>
    <p>Highly trained crew staffing and contract pilot solutions.</p>
    <span class="go"><svg width="12" height="12" viewBox="0 0 12 12"><path d="M1 6h9M7 3l3 3-3 3" stroke="#fff" fill="none" stroke-width="1.2"/></svg></span>
  </article>
  <article class="service-card" style="left:811px;width:389px">
    <div class="photo" role="img" aria-label="Travellers disembarking from an aircraft stairway" style="background:linear-gradient(180deg,#aec0d1 0%,#6f8194 55%,#161e2c 100%)"></div>
    <h3>Trip Support</h3>
    <p>End-to-end logistics for smooth, efficient flight operations.</p>
    <span class="go"><svg width="12" height="12" viewBox="0 0 12 12"><path d="M1 6h9M7 3l3 3-3 3" stroke="#fff" fill="none" stroke-width="1.2"/></svg></span>
  </article>
</section>

<section class="section unified">
  <div class="photo" role="img" aria-label="Airliner in flight above a dense city skyline with mountains" style="background:linear-gradient(180deg,rgba(0,0,0,0) 0%,rgba(0,0,0,0) 60%,rgba(20,45,30,.25) 100%)"></div>
  <h2 class="heading">A Unified Standard in Aviation Excellence</h2>
  <p>Vireton Aviation Group is a modern aviation organization built to deliver comprehensive, high-performance solutions across the private and corporate aviation landscape. As a parent company overseeing multiple specialized subsidiaries, we bring together expertise in aircraft management, acquisition, charter services, pilot staffing, and operational support—under one unified standard of excellence.</p>
  <a class="btn btn-white" href="#">Learn More About Us <svg viewBox="0 0 16 10"><path d="M1 5h13M10 1l4 4-4 4" stroke="#0b5cad" fill="none" stroke-width="1.4"/></svg></a>
  <a class="btn btn-outline" href="#">Explore Services <svg viewBox="0 0 16 10"><path d="M1 5h13M10 1l4 4-4 4" stroke="#23324a" fill="none" stroke-width="1.4"/></svg></a>
</section>

<section class="section testimonial">
  <div class="frame-lines"></div>
  <div class="photo pilot" role="img" aria-label="Captain in uniform standing beside the open door of a private jet" style="background:linear-gradient(180deg,#b7cde3 0%,#dfe6ec 45%,#8f9aa6 100%)"></div>
  <div class="quote-box">
    <h2 class="heading"><span>Trusted</span> by Aviation Professionals and Clients Worldwide</h2>
    <div class="reviewer"><span class="avatar"></span><div><strong>Charter Client</strong><small>1 week ago</small></div></div>
    <blockquote>Vireton Aviation Group has transformed the way we manage our aircraft. Their attention to detail, proactive updates, and commitment to safety give us complete confidence in every flight.</blockquote>
    <div class="stars">
      <svg width="13" height="13" viewBox="0 0 12 12"><path d="M6 .5l1.6 3.4 3.7.4-2.8 2.5.8 3.7L6 8.6 2.7 10.5l.8-3.7L.7 4.3l3.7-.4z" fill="#f5b400"/></svg>
      <svg width="13" height="13" viewBox="0 0 12 12"><path d="M6 .5l1.6 3.4 3.7.4-2.8 2.5.8 3.7L6 8.6 2.7 10.5l.8-3.7L.7 4.3l3.7-.4z" fill="#f5b400"/></svg>
      <svg width="13" height="13" viewBox="0 0 12 12"><path d="M6 .5l1.6 3.4 3.7.4-2.8 2.5.8 3.7L6 8.6 2.7 10.5l.8-3.7L.7 4.3l3.7-.4z" fill="#f5b400"/></svg>
      <svg width="13" height="13" viewBox="0 0 12 12"><path d="M6 .5l1.6 3.4 3.7.4-2.8 2.5.8 3.7L6 8.6 2.7 10.5l.8-3.7L.7 4.3l3.7-.4z" fill="#f5b400"/></svg>
      <svg width="13" height="13" viewBox="0 0 12 12"><path d="M6 .5l1.6 3.4 3.7.4-2.8 2.5.8 3.7L6 8.6 2.7 10.5l.8-3.7L.7 4.3l3.7-.4z" fill="#f5b400"/></svg>
    </div>
    <svg class="quote-mark" width="50" height="40" viewBox="0 0 50 40"><path d="M4 2h18v18l-8 18H6l6-16H4zM28 2h18v18l-8 18h-8l6-16h-8z" fill="#e3ebf5"/></svg>
  </div>
</section>

<section class="section cta">
  <h2 class="heading">Let’s Elevate Your Aviation Experience</h2>
  <p>Connect with our team to explore tailored aviation solutions.</p>
  <a class="btn btn-white" href="#">Request Consultation <svg viewBox="0 0 16 10"><path d="M1 5h13M10 1l4 4-4 4" stroke="#0b5cad" fill="none" stroke-width="1.4"/></svg></a>
  <a class="btn btn-outline" href="#">Speak With an Expert <svg viewBox="0 0 16 10"><path d="M1 5h13M10 1l4 4-4 4" stroke="#fff" fill="none" stroke-width="1.4"/></svg></a>
  <div class="cta-word">VIRETON</div>
</section>

<footer class="section site-footer">
  <div class="footer-brand"><span class="brand-mark"></span><span class="brand-name">Vireton Aviation Group</span></div>
  <p class="footer-about">Vireton Aviation Group delivers integrated aviation solutions across aircraft management, charter, acquisition, and pilot services.</p>
  <div class="socials"><span></span><span></span><span></span></div>

  <div class="fdiv" style="left:300px"></div>
  <div class="fcol" style="left:325px"><h5>COMPANY</h5><ul><li>About</li><li>Aircraft Management</li><li>Aircraft Acquisition</li><li>Charter</li><li>Pilot Services</li><li>Trip Support</li><li>Contact</li></ul></div>

  <div class="fdiv" style="left:488px"></div>
  <div class="fcol" style="left:507px"><h5>CONTACT US</h5>
    <div class="contact-row"><i><svg width="9" height="11" viewBox="0 0 9 11"><path d="M4.5 10S1 6.5 1 4.2a3.5 3.5 0 0 1 7 0C8 6.5 4.5 10 4.5 10z" stroke="#c9d3e2" fill="none"/><circle cx="4.5" cy="4.2" r="1.2" fill="#c9d3e2"/></svg></i><span>402 Harborline Dr, Clearwater, FL, United States</span></div>
    <div class="contact-row"><i><svg width="10" height="10" viewBox="0 0 10 10"><path d="M2 1l2 2-1 1.5a6 6 0 0 0 2.5 2.5L7 6l2 2-1.5 1.5C4 9 1 6 .5 2.5z" fill="#c9d3e2"/></svg></i><span>+1 800-555-0147</span></div>
    <div class="contact-row"><i><svg width="10" height="8" viewBox="0 0 10 8"><rect x=".5" y=".5" width="9" height="7" stroke="#c9d3e2" fill="none"/><path d="M.5 .5L5 4.5 9.5.5" stroke="#c9d3e2" fill="none"/></svg></i><a href="#">info@viretonaviation.com</a></div>
  </div>

  <div class="fdiv" style="left:713px"></div>
  <div class="fcol" style="left:738px"><h5>HOTLINE HOURS</h5><ul><li>Aircraft Management</li><li>Aircraft Acquisition</li><li>Charter Services</li><li>Pilot Services</li><li>Trip Support</li></ul></div>

  <div class="fcol" style="left:934px"><h5>SUBSCRIBE NEWSLETTER</h5>
    <div class="email-field">Enter Your Email</div>
    <a class="btn btn-solid sub-btn" href="#">Subscribe <svg viewBox="0 0 16 10"><path d="M1 5h13M10 1l4 4-4 4" stroke="#fff" fill="none" stroke-width="1.4"/></svg></a>
    <div class="member"><span class="badge"></span><div><small>member of</small><b>PJFO</b></div></div>
  </div>

  <div class="footer-rule"></div>
  <p class="copyright">Copyright © 2026 Vireton Aviation Group. All Rights Reserved</p>
</footer>

</body>
</html>
```